Classy, Elegant, Simple Business Card Design

Looking to have a classy, simple, and elegant design. Want a top notch designed business card. I really like the look of the new torvane credit card. I also like the design I attached. I am trying to reach 21-29 year old females for booking us for there wedding or event. We offer Disc Jockey Service, Photo Booth Rentals, and Uplighting .

Target Market(s)

21-28 year old females

Contact Information for Business Card

Has to have logo, website, email, and phone number

Font styles to use
Other font styles liked:
• open to font choice, modern, clean
Designer to choose
33a6d7
0791cd
0555a3
ffffff

Requirements
Must have
• Has to have logo, website, email, and phone number
Nice to have
• I really like the design of the new torvane credit card. I also included my logo and some designs I like
Should not have
• clutter or too much info

```html
<!DOCTYPE html>
<html lang="en">
<head>
<meta charset="UTF-8">
<title>Tidewell Event Group – Business Card</title>
<link rel="stylesheet" href="https://fonts.googleapis.com/css2?family=Josefin+Sans:wght@300;400;600&family=Work+Sans:wght@400;500&display=swap">
<style>
  :root {
    --navy: #14305a;
    --deep-blue: #0555a3;
    --bright-blue: #0791cd;
    --sky-blue: #33a6d7;
    --white: #ffffff;
    --grey: #8a8f96;
    --text: #4a4f57;
    --stage: #e9ecf0;
  }
  * { box-sizing: border-box; margin: 0; padding: 0; }
  html, body { width: 1200px; height: 912px; overflow: hidden; }
  body {
    background: var(--stage);
    position: relative;
    font-family: "Work Sans", sans-serif;
  }
  .card {
    position: absolute;
    width: 600px;
    height: 343px;
    border-radius: 18px;
    overflow: hidden;
    box-shadow: 0 10px 28px rgba(20, 48, 90, 0.22);
  }

  /* Back side */
  .card--back {
    left: 60px;
    top: 80px;
    background: var(--navy);
    color: var(--white);
  }
  .card--back .brand {
    position: absolute;
    left: 0; right: 0; top: 112px;
    text-align: center;
  }
  .brand__name {
    font-family: "Josefin Sans", sans-serif;
    font-weight: 600;
    letter-spacing: 3px;
    line-height: 1;
  }
  .brand__mark {
    display: inline-block;
    border-radius: 50%;
    vertical-align: middle;
  }
  .brand__tagline {
    font-family: "Josefin Sans", sans-serif;
    font-weight: 300;
    letter-spacing: 8px;
    color: var(--grey);
  }
  .card--back .brand__name { font-size: 50px; color: var(--sky-blue); }
  .card--back .brand__mark { width: 16px; height: 16px; background: var(--sky-blue); margin-right: 12px; margin-top: -10px; }
  .card--back .brand__tagline { font-size: 15px; margin-top: 12px; color: #b9c4d3; }
  .card--back .website {
    position: absolute;
    left: 0; right: 0; bottom: 42px;
    text-align: center;
    font-size: 16px;
    letter-spacing: 2px;
  }

  /* Front side */
  .card--front {
    left: 540px;
    top: 480px;
    background: var(--white);
  }
  .card--front .swoosh {
    position: absolute;
    left: 0; top: 0;
    width: 600px; height: 343px;
  }
  .card--front .brand {
    position: absolute;
    left: 34px; top: 108px;
    width: 260px;
  }
  .card--front .brand__name { font-size: 38px; color: var(--deep-blue); white-space: nowrap; }
  .card--front .brand__mark { width: 12px; height: 12px; background: var(--bright-blue); margin-right: 8px; margin-top: -8px; }
  .card--front .brand__tagline { font-size: 13px; margin-top: 10px; padding-left: 22px; }
  .divider {
    position: absolute;
    left: 312px; top: 48px;
    width: 1.5px; height: 152px;
    background: var(--deep-blue);
  }
  .contact {
    position: absolute;
    left: 334px; top: 36px;
    width: 250px;
    color: var(--text);
    font-size: 13px;
    line-height: 1.45;
  }
  .contact__name {
    font-family: "Josefin Sans", sans-serif;
    font-weight: 600;
    font-size: 21px;
    color: var(--bright-blue);
    letter-spacing: 0.5px;
  }
  .contact__role { margin-bottom: 8px; }
  .contact__address { margin-bottom: 8px; }
  .contact__line { display: flex; align-items: center; gap: 8px; white-space: nowrap; }
  .contact__line svg { width: 11px; height: 11px; flex: none; }
  .contact__accent { color: var(--bright-blue); }
</style>
</head>
<body>

  <section class="card card--back" aria-label="Business card, back">
    <div class="brand">
      <div class="brand__name"><span class="brand__mark"></span>TIDEWELL</div>
      <div class="brand__tagline">EVENT GROUP</div>
    </div>
    <div class="website">www.tidewellevents.com</div>
  </section>

  <section class="card card--front" aria-label="Business card, front">
    <svg class="swoosh" viewBox="0 0 600 343" preserveAspectRatio="none" aria-hidden="true">
      <path d="M0 296 Q 320 318 600 222 L600 343 L0 343 Z" fill="var(--navy)"/>
      <path d="M150 300 Q 390 292 600 208 L600 218 Q 390 306 150 302 Z" fill="var(--deep-blue)"/>
    </svg>

    <div class="brand">
      <div class="brand__name"><span class="brand__mark"></span>TIDEWELL</div>
      <div class="brand__tagline">EVENT GROUP</div>
    </div>

    <div class="divider"></div>

    <div class="contact">
      <div class="contact__name">DANIEL REYES</div>
      <div class="contact__role">Managing Partner</div>
      <div class="contact__address">418 W Harbor Ave.,<br>Bayview, CA 90231</div>
      <div class="contact__line">
        <svg viewBox="0 0 12 12" aria-hidden="true"><path d="M2.5 1 L4.5 1 L5.2 3.6 L4 4.6 Q5 6.9 7.4 8 L8.4 6.8 L11 7.5 L11 9.5 Q10.5 11 9 11 Q1 10 1 3 Q1 1.5 2.5 1 Z" fill="var(--deep-blue)"/></svg>
        <span>555-204-3187</span>
      </div>
      <div class="contact__line">
        <svg viewBox="0 0 12 12" aria-hidden="true"><rect x="1" y="2.5" width="10" height="7" fill="none" stroke="var(--deep-blue)" stroke-width="1.3"/><path d="M1 2.5 L6 6.5 L11 2.5" fill="none" stroke="var(--deep-blue)" stroke-width="1.3"/></svg>
        <span>info@tidewellevents.com</span>
      </div>
      <div class="contact__line">
        <svg viewBox="0 0 12 12" aria-hidden="true"><circle cx="6" cy="6" r="5" fill="none" stroke="var(--deep-blue)" stroke-width="1.2"/><ellipse cx="6" cy="6" rx="2.2" ry="5" fill="none" stroke="var(--deep-blue)" stroke-width="1"/><line x1="1" y1="6" x2="11" y2="6" stroke="var(--deep-blue)" stroke-width="1"/></svg>
        <span>www.<span class="contact__accent">tidewellevents</span>.com</span>
      </div>
    </div>
  </section>

</body>
</html>
```